Redesign and move to Wordpress for corvandel.com

Our website needs a redesign and at the same time we are moving it to Wordpress. Please help us with a new digital professional look and feel.

We are an Australian Software Engineering company specialising in advanced software development using in A.I., PLatform Engineering, Integration and Cloud. See the current corvandel.com for more information about us.

```html
<!DOCTYPE html>
<html lang="en">
<head>
<meta charset="utf-8">
<title>Corvandel — Reliable Smart Software Engineering</title>
<link href="https://fonts.googleapis.com/css2?family=Poppins:wght@300;400;500;600;700&display=swap" rel="stylesheet">
<style>
:root{
  --navy:#061127;
  --blue:#1b4e8a;
  --blue-deep:#143f78;
  --footer:#1c4f92;
  --teal:#4cc4bc;
  --teal-soft:#7fd8d1;
  --ink:#222;
  --muted:#444;
  --line:#e7e9ee;
  --white:#fff;
}
*{box-sizing:border-box;margin:0;padding:0}
html,body{width:1200px;height:4587px;overflow:hidden}
body{font-family:'Poppins',sans-serif;color:var(--ink);background:var(--white);position:relative}
.abs{position:absolute}
.btn{position:absolute;display:flex;align-items:center;justify-content:center;gap:10px;background:var(--blue);color:var(--white);font-size:14px;font-weight:400;letter-spacing:.3px;text-transform:uppercase}
.btn .tip{width:11px;height:11px;background:var(--teal);display:inline-block;position:relative}
.btn .tip::after{content:"";position:absolute;left:3px;top:2px;border-left:5px solid var(--blue);border-top:3.5px solid transparent;border-bottom:3.5px solid transparent}
.btn.teal{background:var(--teal)}
.btn.teal .tip{background:var(--blue)}
.btn.teal .tip::after{border-left-color:var(--teal)}
.brand{display:flex;align-items:center;gap:12px;font-size:30px;font-weight:300;color:var(--white);letter-spacing:1px}
.brand .mark{width:34px;height:34px;border:3px solid var(--teal)}

/* hero */
.hero-bg{left:0;top:0;width:1200px;height:801px;background:radial-gradient(circle at 960px 520px,#2f8fc0 0,#0f3e6c 22%,transparent 45%),radial-gradient(circle at 700px 250px,#0f3a63 0,transparent 30%),linear-gradient(180deg,#050d1f 0%,#071730 70%,#0a2440 100%)}
.nav{left:690px;top:50px;display:flex;gap:0;font-size:13px;color:var(--white)}
.nav a{position:absolute;white-space:nowrap;color:var(--white);text-decoration:none}
.nav .active{color:var(--teal-soft);border-bottom:1px solid var(--teal-soft);padding-bottom:4px}
.nav-contact{left:1032px;top:44px;width:103px;height:28px;background:var(--blue);color:var(--white);font-size:13px;display:flex;align-items:center;justify-content:center}
.hero-title{left:66px;top:248px;font-size:47px;font-weight:400;color:var(--white);line-height:58px;letter-spacing:.5px}
.hero-text{left:68px;top:386px;width:520px;font-size:15px;line-height:29px;color:var(--white)}

/* section heads */
.h-big{font-size:46px;font-weight:400;color:var(--ink)}
.eyebrow{font-size:18px;color:var(--blue);font-weight:500;display:flex;align-items:center;gap:10px}
.eyebrow .dash{display:inline-block;height:2px;background:var(--blue);position:relative}
.eyebrow .dot{width:8px;height:8px;background:var(--blue);display:inline-block}

/* about */
.about-text{left:110px;top:1050px;width:520px;font-size:13px;line-height:25px;color:var(--ink)}
.about-text p{margin-bottom:24px}
.tile{position:absolute;border:10px solid var(--blue)}
.tile.teal{border-color:var(--teal)}

/* services */
.card{position:absolute;top:1696px;width:322px;height:324px;background:var(--white);border-radius:18px;box-shadow:0 4px 22px rgba(0,0,0,.08);text-align:center;padding-top:44px}
.card.focus{border:2px solid var(--teal)}
.card .icon{width:74px;height:72px;margin:0 auto;background:var(--blue);display:flex;align-items:center;justify-content:center;border-radius:3px}
.card.focus .icon{background:var(--teal)}
.card h3{margin-top:24px;font-size:20px;line-height:25px;font-weight:400;color:var(--blue)}
.card .rule{width:40px;height:1px;background:#bbb;margin:10px auto 14px}
.card p{font-size:13px;line-height:24px;color:var(--muted);width:240px;margin:0 auto}
.card .go{width:32px;height:32px;border-radius:50%;background:var(--teal);margin:16px auto 0;display:flex;align-items:center;justify-content:center}

/* banner */
.banner{left:0;top:2303px;width:1200px;height:454px;background:linear-gradient(90deg,#030a14 0%,#0b2a3c 28%,#2a5660 40%,#e9ecee 52%,#eef0f2 100%)}
.banner-copy{left:528px;top:2400px;width:596px;text-align:center}
.banner-copy p{font-size:15px;line-height:24px;color:var(--ink)}
.banner-copy h2{margin-top:22px;font-size:29px;line-height:50px;font-weight:600;color:var(--blue);text-transform:uppercase}

/* blog */
.post{position:absolute;top:2981px;width:330px;height:490px;background:var(--white);box-shadow:0 3px 18px rgba(0,0,0,.09);padding:8px}
.post .pic{height:235px}
.post .body{padding:14px 6px 0}
.post .date{font-size:13px;color:var(--teal);display:flex;align-items:center;gap:5px}
.post .date i{width:10px;height:10px;background:var(--teal);display:inline-block}
.post h3{margin-top:8px;font-size:16px;line-height:25px;font-weight:600;color:var(--blue)}
.post .tags{font-size:13px;font-style:italic;color:var(--muted);margin-top:6px}
.post p{font-size:13px;line-height:24px;color:var(--muted);margin-top:6px}
.post .more{margin-top:8px;display:inline-block;background:var(--blue);color:var(--white);font-size:12px;padding:6px 16px;text-transform:uppercase}
.arrow{position:absolute;top:3208px;width:34px;height:34px;border-radius:50%;border:1px solid #ccc;background:var(--white);display:flex;align-items:center;justify-content:center}

/* contact */
.field{position:absolute;background:var(--white);box-shadow:0 2px 12px rgba(0,0,0,.08);font-size:16px;color:#666;padding:18px 28px}

/* footer */
.footer{left:0;top:4227px;width:1200px;height:313px;background:var(--footer);color:var(--white)}
.divider{position:absolute;top:40px;width:1px;height:240px;background:rgba(255,255,255,.35)}
.fhead{position:absolute;top:84px;font-size:16px;font-weight:500;display:flex;align-items:center;gap:24px;text-transform:uppercase}
.fhead i{width:9px;height:9px;background:var(--white);display:inline-block}
.flinks a{position:absolute;display:flex;align-items:center;gap:8px;font-size:14px;color:var(--white);text-decoration:none}
.flinks a i{width:11px;height:11px;border:1px solid var(--white);display:inline-block}
.finfo{position:absolute;display:flex;gap:14px;font-size:13px;line-height:16px}
.finfo .ic{width:26px;height:26px;border:1px solid rgba(255,255,255,.6);border-radius:3px;display:flex;align-items:center;justify-content:center;flex:none}
.copy{left:0;top:4540px;width:1200px;height:47px;background:var(--teal);color:var(--white);font-size:12px;display:flex;align-items:center;justify-content:center}
</style>
</head>
<body>

<!-- HERO -->
<div class="abs hero-bg" role="img" aria-label="Dark technology background with glowing data lines and a hand holding holographic icons of a check mark, globe, analytics and settings"></div>
<div class="abs brand" style="left:68px;top:20px"><span class="mark"></span>corvandel</div>
<nav class="abs nav">
  <a class="active" style="left:0;top:0">Home</a>
  <a style="left:83px;top:0">Services</a>
  <a style="left:182px;top:0">About</a>
  <a style="left:265px;top:0">Blog</a>
</nav>
<div class="abs nav-contact">Contact</div>
<h1 class="abs hero-title">RELIABLE SMART<br>SOFTWARE ENGINEERING</h1>
<p class="abs hero-text">We have been on a mission to make complex custom enterprise integration accessible to any organisation, regardless of industry, size, or location.</p>
<div class="btn" style="left:68px;top:543px;width:156px;height:34px">Contact Us <span class="tip"></span></div>

<!-- ABOUT -->
<h2 class="abs h-big" style="left:110px;top:928px">About Us</h2>
<div class="abs eyebrow" style="left:110px;top:992px">WHO WE ARE <span class="dot"></span><span class="dash" style="width:60px;margin-left:-10px"></span></div>
<div class="abs about-text">
  <p>Welcome to Corvandel!</p>
  <p>Since our inception in 2013, we have been on a mission to make complex custom enterprise integration accessible to any organization, regardless of industry, size, or location.</p>
  <p>Our journey began with a focus on Integration Architecture, quickly moving into delivering bespoke systems integration using Vantrix technologies like FlowBridge, CoreNet, Strata SQL, and ServiceLink.</p>
</div>
<div class="btn" style="left:110px;top:1310px;width:155px;height:36px">Know More <span class="tip"></span></div>

<div class="tile" style="left:675px;top:955px;width:190px;height:130px;background:linear-gradient(135deg,#1d3fd0,#0a1a8a)" role="img" aria-label="Abstract blue technology graphic"></div>
<div class="tile" style="left:892px;top:955px;width:190px;height:262px;background:linear-gradient(160deg,#0a1560,#0b0f3d)" role="img" aria-label="Dark blue circular data interface graphic"></div>
<div class="tile teal" style="left:675px;top:1113px;width:190px;height:262px;background:linear-gradient(160deg,#3a1f8a,#7a1670 60%,#2a0c50)" role="img" aria-label="Purple cloud technology graphic"></div>
<div class="tile teal" style="left:892px;top:1246px;width:190px;height:130px;background:linear-gradient(90deg,#0a1560 55%,#d9b8a0)" role="img" aria-label="Hand touching a digital interface"></div>

<!-- SERVICES -->
<h2 class="abs h-big" style="left:0;width:1200px;text-align:center;top:1545px">Our Services</h2>
<div class="abs eyebrow" style="left:452px;top:1612px"><span class="dash" style="width:60px"></span><span class="dot" style="margin-left:-10px"></span> WHAT WE DO <span class="dot"></span><span class="dash" style="width:60px;margin-left:-10px"></span></div>

<div class="card" style="left:78px">
  <div class="icon"><svg width="50" height="40" viewBox="0 0 50 40" fill="none" stroke="#fff" stroke-width="1.6"><circle cx="10" cy="8" r="4"/><circle cx="25" cy="8" r="4"/><circle cx="40" cy="8" r="4"/><circle cx="10" cy="20" r="4"/><circle cx="25" cy="20" r="4"/><circle cx="40" cy="20" r="4"/><circle cx="10" cy="32" r="4"/><circle cx="25" cy="32" r="4"/><circle cx="40" cy="32" r="4"/><path d="M14 20h7M29 20h7"/></svg></div>
  <h3>Enterprise Systems<br>Integration</h3>
  <div class="rule"></div>
  <p>Enterprise systems integration is the process of connecting various IT systems, applications, and data</p>
</div>
<div class="card focus" style="left:440px">
  <div class="icon"><svg width="50" height="46" viewBox="0 0 50 46" fill="none" stroke="#fff" stroke-width="1.6"><circle cx="25" cy="23" r="7"/><circle cx="25" cy="5" r="3"/><circle cx="25" cy="41" r="3"/><circle cx="6" cy="23" r="3"/><circle cx="44" cy="23" r="3"/><circle cx="10" cy="9" r="3"/><circle cx="40" cy="37" r="3"/><path d="M25 8v8M25 30v8M9 23h9M32 23h9M12 11l8 7M30 28l8 7"/></svg></div>
  <h3>Microservices</h3>
  <div class="rule"></div>
  <p>Microservices is an architectural style that structures an application as a collection of small, autono-</p>
  <div class="go"><svg width="14" height="14" viewBox="0 0 14 14" fill="none" stroke="#fff" stroke-width="1.8"><path d="M2 7h9M7 3l4 4-4 4"/></svg></div>
</div>
<div class="card" style="left:792px">
  <div class="icon"><svg width="46" height="44" viewBox="0 0 46 44" fill="none" stroke="#fff" stroke-width="1.6"><path d="M12 30a9 9 0 0 1 1-18 11 11 0 0 1 21 3 8 8 0 0 1-1 15z"/><circle cx="23" cy="21" r="5"/><path d="M23 13v3M23 26v3M15 21h3M28 21h3M15 38h16"/></svg></div>
  <h3>PLatform Engineering</h3>
  <div class="rule"></div>
  <p>Platform engineering involves cre-ating and managing the tools and processes that allow software</p>
</div>
<div class="btn" style="left:492px;top:2118px;width:224px;height:57px;font-size:15px">View All Services <span class="tip"></span></div>

<!-- BANNER -->
<div class="abs banner" role="img" aria-label="Open hand reaching toward glowing digital network lines on a dark background"></div>
<div class="abs banner-copy">
  <p>At Corvandel, we craft bespoke software solutions that are not available on the market. By building organizations market-leading products, process automation, legacy system enablement, or advanced intelligent systems</p>
  <h2>We empower our customers to achieve a competitive edge in their industry.</h2>
</div>
<div class="btn teal" style="left:745px;top:2655px;width:155px;height:34px">Contact Us <span class="tip"></span></div>

<!-- BLOG -->
<h2 class="abs h-big" style="left:0;width:1200px;text-align:center;top:2848px">Our Blog</h2>
<div class="abs eyebrow" style="left:488px;top:2910px"><span class="dash" style="width:24px"></span><span class="dot" style="margin-left:-10px"></span>NEWS &amp; UPDATES<span class="dot"></span><span class="dash" style="width:24px;margin-left:-10px"></span></div>

<div class="arrow" style="left:16px"><svg width="10" height="10" viewBox="0 0 10 10" fill="none" stroke="#333" stroke-width="1.5"><path d="M6.5 1.5 3 5l3.5 3.5"/></svg></div>
<div class="arrow" style="left:1154px"><svg width="10" height="10" viewBox="0 0 10 10" fill="none" stroke="#333" stroke-width="1.5"><path d="M3.5 1.5 7 5 3.5 8.5"/></svg></div>

<article class="post" style="left:78px">
  <div class="pic" role="img" aria-label="Rows of server racks with green lights in a data centre" style="background:linear-gradient(90deg,#0b1e12,#2f6a2a 30%,#0c1a10 50%,#3b7a30 75%,#0b1e12)"></div>
  <div class="body">
    <div class="date"><i></i>June 24, 2024</div>
    <h3>Why most upgrade paths for Flow-Bridge lead to using Nimbus Logic apps</h3>
    <div class="tags">Integration, FlowBridge</div>
    <p>Introduction In today's fast-evolving technological landscape, businesses</p>
    <span class="more">Know More</span>
  </div>
</article>
<article class="post" style="left:438px">
  <div class="pic" role="img" aria-label="Team meeting around a table with a laptop and diagrams" style="background:linear-gradient(160deg,#d9dee4,#8d949c 55%,#a07a52)"></div>
  <div class="body">
    <div class="date"><i></i>June 21, 2024</div>
    <h3>Meet Corvandel: The FlowBridge Experts</h3>
    <div class="tags">Integration, FlowBridge,Vantrix</div>
    <p>At Corvandel, we pride ourselves on having a team of exceptional talent,</p>
    <span class="more">Know More</span>
  </div>
</article>
<article class="post" style="left:795px">
  <div class="pic" role="img" aria-label="Illustration of a worried developer beside a server rack and stacks of paperwork" style="background:linear-gradient(90deg,#e9ecf0,#2a3550 40%,#c33 55%,#2a3550 70%,#e9ecf0)"></div>
  <div class="body">
    <div class="date"><i></i>June 24, 2024</div>
    <h3>Top Reasons FlowBridge Server Run-time Can Fail in Production</h3>
    <div class="tags">Integration, FlowBridge</div>
    <p>As a FlowBridge expert with extensive experi-ence in deploying and maintaining</p>
    <span class="more">Know More</span>
  </div>
</article>

<!-- CONTACT -->
<div class="abs" style="left:52px;top:3676px;width:144px;height:124px;background:var(--teal)"></div>
<div class="abs" style="left:52px;top:4060px;width:148px;height:165px;background:var(--blue)"></div>
<div class="abs" role="img" aria-label="Developer working on a laptop surrounded by coding icons" style="left:72px;top:3705px;width:406px;height:460px;background:linear-gradient(160deg,#3d5f86,#8fa6bf 45%,#c9b29a 70%,#5b7390)"></div>

<h2 class="abs" style="left:565px;top:3705px;font-size:50px;font-weight:400">Contact Us</h2>
<div class="abs eyebrow" style="left:573px;top:3770px">CORVANDEL <span class="dot" style="width:6px;height:6px"></span><span class="dash" style="width:55px;margin-left:-10px"></span></div>
<p class="abs" style="left:577px;top:3810px;font-size:13px">Fill out our form and we'll be in touch.</p>
<div class="field" style="left:573px;top:3853px;width:269px;height:57px">First Name</div>
<div class="field" style="left:862px;top:3853px;width:270px;height:57px">Last Name</div>
<div class="field" style="left:573px;top:3922px;width:269px;height:57px">Mobile Number</div>
<div class="field" style="left:862px;top:3922px;width:270px;height:57px">Email Address</div>
<div class="field" style="left:573px;top:3990px;width:562px;height:95px">Message</div>
<div class="btn" style="left:577px;top:4115px;width:135px;height:34px;font-size:15px">Submit <span class="tip"></span></div>

<!-- FOOTER -->
<footer class="abs footer">
  <div class="abs brand" style="left:68px;top:72px;font-size:24px;gap:10px"><span class="mark" style="width:28px;height:28px"></span>corvandel</div>
  <p class="abs" style="left:68px;top:135px;width:220px;font-size:13px;line-height:24px">We have been on a mission to make complex custom enter-prise integration accessible to any organisation,</p>
  <div class="abs" style="left:78px;top:270px;display:flex;gap:8px">
    <span style="width:26px;height:26px;border-radius:50%;background:var(--teal)"></span>
    <span style="width:26px;height:26px;border-radius:50%;border:2px solid var(--white)"></span>
    <span style="width:26px;height:26px;border-radius:50%;border:2px solid var(--white)"></span>
  </div>

  <div class="divider" style="left:340px"></div>
  <div class="divider" style="left:597px"></div>
  <div class="divider" style="left:890px"></div>

  <div class="fhead" style="left:334px"><i></i>Quick Links</div>
  <div class="flinks">
    <a style="left:375px;top:138px"><i></i>Home</a>
    <a style="left:375px;top:164px"><i></i>Services</a>
    <a style="left:375px;top:190px"><i></i>Contact</a>
    <a style="left:375px;top:216px"><i></i>About</a>
    <a style="left:375px;top:242px"><i></i>Blog</a>
  </div>

  <div class="fhead" style="left:592px"><i></i>Contact Us</div>
  <div class="finfo" style="left:622px;top:130px"><span class="ic"><svg width="12" height="12" viewBox="0 0 12 12" fill="none" stroke="#fff" stroke-width="1.2"><path d="M2 1h2.5l1 3-1.5 1a7 7 0 0 0 3 3l1-1.5 3 1V10a1 1 0 0 1-1 1A10 10 0 0 1 1 2a1 1 0 0 1 1-1z"/></svg></span><div>CALL US<br>1800 555 019</div></div>
  <div class="finfo" style="left:622px;top:182px"><span class="ic"><svg width="12" height="10" viewBox="0 0 12 10" fill="none" stroke="#fff" stroke-width="1.2"><rect x=".6" y=".6" width="10.8" height="8.8"/><path d="M.6.6 6 5 11.4.6"/></svg></span><div>EMAIL US<br>hello@corvandel.com</div></div>
  <div class="finfo" style="left:622px;top:234px"><span class="ic"><svg width="10" height="13" viewBox="0 0 10 13" fill="none" stroke="#fff" stroke-width="1.2"><path d="M5 12S1 7.5 1 5a4 4 0 0 1 8 0c0 2.5-4 7-4 7z"/><circle cx="5" cy="5" r="1.5"/></svg></span><div>Suite 402, 18 Harbour Lane<br>Melbourne, VIC , 3004</div></div>

  <div class="fhead" style="left:890px"><i></i>Newsletter Sign Up</div>
  <p class="abs" style="left:927px;top:144px;width:200px;font-size:13px;line-height:18px">Subscribe our newsletter to get the latest news.</p>
  <div class="abs" style="left:920px;top:205px;width:205px;height:36px;border:1px solid var(--white);border-radius:18px;font-size:12px;padding:9px 16px">Enter Email Address</div>
  <div class="abs" style="left:1093px;top:212px;width:22px;height:22px;border:1px solid var(--white);border-radius:50%;display:flex;align-items:center;justify-content:center"><svg width="10" height="10" viewBox="0 0 10 10" fill="none" stroke="#fff" stroke-width="1.3"><path d="M1 5h7M5 2l3 3-3 3"/></svg></div>
</footer>
<div class="abs copy">Copyright © 2025 All Rights Reserved By Corvandel | Privacy Policy</div>

</body>
</html>
```